Computer consultant business card

Bexil Software is a newly started computer consulting company. It's a small one-man company that provides mostly Vornix applications but also websites in collaboration with designers. I'm running this company on the side of full time university studies.

I want the final design to be clean and memorable. Be creative! :)

Some inspiration:
http://www.pixelmarta.com/design/48317
http://www.pixelmarta.com/design/2739164/business-card-design-by-frostlynk
http://www.pixelmarta.com/design/604281/business-card-design-by-koralind-vestrabanu

See attachment for my company logo.
Updates

I would like to thank everyone for submitting! I'll need a couple of days to review and ultimately select a design.

Target Market(s)

Non-technical entrepreneurs and small companies.

Industry/Entity Type

University

Requirements
Must have
• My company logo.
In any way, both colors from my logo.
First- and last name, e-mail and phone number.
Double-sided design.
Nice to have
• Something creative with the symbol in my logo

```html
<!DOCTYPE html>
<html lang="en">
<head>
<meta charset="utf-8">
<title>Bexil Software – Business Card</title>
<link href="https://fonts.googleapis.com/css2?family=Jost:wght@400;500&display=swap" rel="stylesheet">
<style>
  :root {
    --page-bg: #e9e9eb;
    --card-bg: #ffffff;
    --brand-blue: #2a7ff0;
    --brand-dark: #353132;
    --text-dark: #2a2a2a;
    --rule-grey: #8a8a8a;
  }
  * { margin: 0; padding: 0; box-sizing: border-box; }
  html, body {
    width: 1200px;
    height: 823px;
    overflow: hidden;
    background: var(--page-bg);
    font-family: "Jost", "Futura", sans-serif;
  }
  .sheet {
    position: relative;
    width: 1200px;
    height: 823px;
  }
  .card {
    position: absolute;
    width: 560px;
    height: 320px;
    background: var(--card-bg);
    box-shadow: 0 2px 10px rgba(0,0,0,0.18);
    overflow: hidden;
  }
  .card--front { left: 60px; top: 110px; }
  .card--back  { left: 580px; top: 400px; }

  /* Front */
  .wordmark {
    position: absolute;
    left: 72px;
    top: 118px;
    display: flex;
    align-items: center;
    gap: 14px;
  }
  .wordmark__dot {
    width: 38px;
    height: 38px;
    border-radius: 50%;
    background: var(--brand-blue);
  }
  .wordmark__name {
    font-size: 52px;
    font-weight: 500;
    line-height: 1;
    color: var(--brand-dark);
    letter-spacing: 1px;
  }
  .contact {
    position: absolute;
    left: 300px;
    top: 42px;
    height: 196px;
    padding-left: 18px;
    border-left: 1px solid var(--rule-grey);
  }
  .contact::before {
    content: "";
    position: absolute;
    left: -2px;
    top: 0;
    width: 4px;
    height: 46px;
    background: var(--brand-blue);
  }
  .contact__first {
    font-size: 20px;
    font-weight: 500;
    color: var(--brand-blue);
    line-height: 1.1;
  }
  .contact__last {
    font-size: 15px;
    color: var(--text-dark);
    margin-bottom: 20px;
  }
  .contact__line {
    display: flex;
    align-items: center;
    gap: 7px;
    font-size: 14px;
    color: var(--text-dark);
    line-height: 1.55;
  }
  .contact__line svg { width: 11px; height: 11px; fill: var(--brand-blue); }
  .contact__address {
    margin-top: 14px;
    font-size: 14px;
    line-height: 1.55;
    color: var(--text-dark);
  }
  .card__bands {
    position: absolute;
    left: 0;
    bottom: 0;
    width: 560px;
    height: 80px;
  }
  .band--blue { fill: var(--brand-blue); }
  .band--dark { fill: var(--brand-dark); }

  /* Back */
  .emblem {
    position: absolute;
    inset: 0;
    display: flex;
    align-items: center;
    justify-content: center;
    gap: 22px;
  }
  .emblem__dot {
    width: 70px;
    height: 70px;
    border-radius: 50%;
    background: var(--brand-blue);
  }
  .emblem__name {
    font-size: 96px;
    font-weight: 500;
    line-height: 1;
    color: var(--brand-dark);
    letter-spacing: 2px;
  }
</style>
</head>
<body>
<main class="sheet">

  <section class="card card--front" aria-label="Card front">
    <div class="wordmark">
      <span class="wordmark__dot"></span>
      <span class="wordmark__name">bexil</span>
    </div>

    <div class="contact">
      <p class="contact__first">First Name</p>
      <p class="contact__last">Last Name</p>
      <p class="contact__line">
        <svg viewBox="0 0 24 24" aria-hidden="true"><path d="M6.6 10.8a15.1 15.1 0 0 0 6.6 6.6l2.2-2.2a1 1 0 0 1 1-.25 11.4 11.4 0 0 0 3.6.6 1 1 0 0 1 1 1V20a1 1 0 0 1-1 1A17 17 0 0 1 3 4a1 1 0 0 1 1-1h3.5a1 1 0 0 1 1 1c0 1.25.2 2.45.6 3.6a1 1 0 0 1-.25 1z"/></svg>
        0612 308754
      </p>
      <p class="contact__line">
        <svg viewBox="0 0 24 24" aria-hidden="true"><path d="M2 5h20v14H2zm2 2v.5l8 5 8-5V7z"/></svg>
        info@bexil.com
      </p>
      <p class="contact__address">14, Harlow Court<br>Brenton, State 0317</p>
    </div>

    <svg class="card__bands" viewBox="0 0 560 80" preserveAspectRatio="none" aria-hidden="true">
      <polygon class="band--blue" points="0,58 280,20 270,80 0,80"/>
      <polygon class="band--dark" points="292,18 560,0 560,24 284,48"/>
    </svg>
  </section>

  <section class="card card--back" aria-label="Card back">
    <div class="emblem">
      <span class="emblem__dot"></span>
      <span class="emblem__name">bexil</span>
    </div>
  </section>

</main>
</body>
</html>
```